Rockin' movie poster/thumbnail for rock musical.

We need a 16x9 poster/thumbnail (both horizontal and vertical) for a rock driven independent film called Crimson Orbit: A Kaleidoscope Heart Tale. The poster/thumbnail will be used for digital streaming platforms.

Crimson Orbit is a very unique film in that it seamlessly combines a mind-bending story with live rock music performance. The film follows a rock band that is hired to record the music for a romance film only to discover that their music is mysteriously altering the story-line.

Target Market(s)

Younger aged music fans and old-school rockers alike. Film influences: Marlowe and the Restless Mile, Tin Harbor's The Gate, Quiet Thunder of the Wandering Soul.

Industry/Entity Type

Indie film and rock music

Font styles to use
Other font styles liked:
• Fonts like Abys and Impact are always fun!

Colors
FFF300
FFF600
FEFA6F
FFFEC7
FFFEE8
EB3D1F
EC4F4E
F09395
F8D3D4
FCEDEE
E54698
E96AAD
F1A4CE
F9D9EA
FCEFF6
A7469A
B969AE
D3A5CF
EDDBEB
F8F0F9
6B429C
8869AF
B7A5CE
E3DAEB
F3F0F8

Requirements
Must have
• Picture of Royce Malden and his name above title. A colorful, hard-hitting rock-n-roll edged design. The thumbnail should scream out FUN, ROCK-N-ROLL MOVIE to people scrolling the digital streaming platforms.
Nice to have
• Vibrant color, attitude.
Should not have
• Sappy romance or drama vibe.

```html
<!DOCTYPE html>
<html lang="en">
<head>
<meta charset="utf-8">
<title>Crimson Orbit – Poster</title>
<link rel="stylesheet" href="https://fonts.googleapis.com/css2?family=Josefin+Sans:wght@400&family=Permanent+Marker&family=Oswald:wght@600&display=swap">
<style>
  :root {
    --page-bg: #ffffff;
    --sky-top: #e89a6a;
    --sky-mid: #b5524a;
    --ground: #3a0f14;
    --ground-deep: #1f0709;
    --banner: #3b3436;
    --banner-text: #f3eee9;
    --pick: #ec4f4e;
    --pick-light: #f09395;
    --title-pink: #f1a4ce;
    --title-pink-deep: #e96aad;
    --tagline: #fff300;
    --rule: #fffee8;
  }
  * { margin: 0; padding: 0; box-sizing: border-box; }
  html, body { width: 1200px; height: 2628px; overflow: hidden; background: var(--page-bg); }
  .poster {
    position: absolute; left: 208px; top: 618px;
    width: 784px; height: 1392px; overflow: hidden;
    box-shadow: 0 6px 18px rgba(0,0,0,.35);
  }
  .poster__backdrop {
    position: absolute; inset: 0;
    background: linear-gradient(180deg, var(--sky-top) 0%, #d9765a 18%, var(--sky-mid) 33%, #5a1a1f 45%, var(--ground) 62%, var(--ground-deep) 100%);
  }
  .poster__halo {
    position: absolute; left: 32px; top: 197px; width: 720px; height: 720px;
    border-radius: 50%; background: rgba(40,8,12,.35);
  }
  .poster__portrait {
    position: absolute; left: 112px; top: 277px; width: 560px; height: 560px;
    border-radius: 50%;
    background: radial-gradient(circle at 55% 40%, #e79aa6 0%, #b9566f 45%, #6e2638 100%);
    opacity: .92;
  }
  .banner {
    position: absolute; left: 62px; top: 60px; width: 660px; height: 60px;
  }
  .banner__band {
    position: absolute; left: 52px; right: 52px; top: 10px; height: 42px;
    background: var(--banner);
  }
  .banner__text {
    position: absolute; left: 0; right: 0; top: 14px;
    text-align: center; font-family: "Josefin Sans", sans-serif;
    font-size: 30px; color: var(--banner-text); letter-spacing: .2px;
  }
  .banner__pick { position: absolute; top: 0; width: 52px; height: 60px; }
  .banner__pick--left { left: 0; }
  .banner__pick--right { right: 0; transform: scaleX(-1); }
  .title { position: absolute; left: 0; right: 0; top: 840px; }
  .title__main {
    position: absolute; left: 88px; top: 0;
    font-family: "Permanent Marker", cursive;
    font-size: 136px; line-height: 1; color: var(--title-pink);
    letter-spacing: -2px;
  }
  .title__sub {
    position: absolute; left: 400px; top: 146px;
    padding: 2px 16px 6px;
    background: var(--title-pink-deep);
    font-family: "Permanent Marker", cursive;
    font-size: 64px; line-height: 1; color: var(--title-pink);
    transform: rotate(-2deg);
  }
  .tagline { position: absolute; left: 80px; width: 624px; top: 1148px; height: 76px; }
  .tagline__rule { position: absolute; left: 22px; right: 12px; height: 4px; background: var(--rule); }
  .tagline__rule--top { top: 0; }
  .tagline__rule--bottom { bottom: 0; }
  .tagline__text {
    position: absolute; left: 0; right: 0; top: 12px;
    text-align: center; font-family: "Oswald", sans-serif; font-weight: 600;
    font-size: 38px; line-height: 50px; color: var(--tagline);
  }
  .tagline__bolt { position: absolute; top: 30px; width: 38px; height: 14px; }
  .tagline__bolt--left { left: 0; }
  .tagline__bolt--right { right: 0; transform: scaleX(-1); }
</style>
</head>
<body>
  <main class="poster">
    <div class="poster__backdrop" role="img" aria-label="Rooftop at sunset with a power pylon and city skyline"></div>
    <div class="poster__halo"></div>
    <div class="poster__portrait" role="img" aria-label="Couple embracing at sunset, tinted pink"></div>

    <div class="banner">
      <div class="banner__band"></div>
      <svg class="banner__pick banner__pick--left" viewBox="0 0 52 60" aria-hidden="true">
        <path d="M26 4 C42 4 50 12 48 24 C46 38 34 52 26 56 C18 52 6 38 4 24 C2 12 10 4 26 4 Z" fill="var(--pick-light)"/>
        <path d="M26 10 C38 10 44 16 42 25 C40 36 32 46 26 49 C20 46 12 36 10 25 C8 16 14 10 26 10 Z" fill="var(--pick)"/>
      </svg>
      <p class="banner__text">ROCK DRIVEN INDEPENDENT FILM</p>
      <svg class="banner__pick banner__pick--right" viewBox="0 0 52 60" aria-hidden="true">
        <path d="M26 4 C42 4 50 12 48 24 C46 38 34 52 26 56 C18 52 6 38 4 24 C2 12 10 4 26 4 Z" fill="var(--pick-light)"/>
        <path d="M26 10 C38 10 44 16 42 25 C40 36 32 46 26 49 C20 46 12 36 10 25 C8 16 14 10 26 10 Z" fill="var(--pick)"/>
      </svg>
    </div>

    <h1 class="title">
      <span class="title__main">CRIMSON</span>
      <span class="title__sub">ORBIT</span>
    </h1>

    <div class="tagline">
      <div class="tagline__rule tagline__rule--top"></div>
      <svg class="tagline__bolt tagline__bolt--left" viewBox="0 0 38 14" aria-hidden="true">
        <path d="M0 4 L20 4 L16 0 L38 8 L18 8 L22 14 Z" fill="var(--tagline)"/>
      </svg>
      <p class="tagline__text">A KALEIDOSCOPE HEART TALE</p>
      <svg class="tagline__bolt tagline__bolt--right" viewBox="0 0 38 14" aria-hidden="true">
        <path d="M0 4 L20 4 L16 0 L38 8 L18 8 L22 14 Z" fill="var(--tagline)"/>
      </svg>
      <div class="tagline__rule tagline__rule--bottom"></div>
    </div>
  </main>
</body>
</html>
```